Lo Mara Menu Design Project

This project is pretty straight forward. You will be given 3 files which include the following:
1. Our proposed menu
2. Our Company logo
3. A sample menu on what we are looking for design wise

Your job is to create a visually pleasing menu that is simple, clean and fresh. Please refer to our home website for additional information. (www.lomara-eats.com) Must be in eps or equivalent format.

Target Market(s)

20s to 40s

Industry/Entity Type

It Company

Requirements
Must have
• Company log
Must be in EPS format

```html
<!DOCTYPE html>
<html lang="en">
<head>
<meta charset="utf-8">
<title>Lo Mara Menu</title>
<link href="https://fonts.googleapis.com/css2?family=Arimo&family=Tinos:wght@700&display=swap" rel="stylesheet">
<style>
  :root{
    --backdrop:#8a5a38;
    --panel-top:#2a2a2a;
    --panel-bottom:#161616;
    --ink:#ffffff;
    --accent:#d8261f;
  }
  html,body{margin:0;padding:0;overflow:hidden}
  body{width:1200px;height:557px;background:var(--backdrop);position:relative;font-family:"Arimo",Arial,sans-serif;color:var(--ink)}
  .menu-panel{
    position:absolute;top:55px;width:338px;height:437px;
    background:linear-gradient(180deg,var(--panel-top),var(--panel-bottom));
    box-shadow:0 4px 12px rgba(0,0,0,.45);
  }
  .panel-left{left:45px}
  .panel-middle{left:426px}
  .panel-right{left:807px}
  .section-title{
    position:absolute;width:160px;margin:0;
    left:calc(var(--x) * 1px - 80px);top:calc(var(--y) * 1px - 15px);
    text-align:center;font-weight:400;font-size:24px;line-height:30px;
  }
  .section-title::after{
    content:"";display:block;width:86px;height:2px;background:var(--accent);margin:1px auto 0;
  }
  .dish{
    position:absolute;width:150px;
    left:calc(var(--x) * 1px - 75px);top:calc(var(--y) * 1px);
    text-align:center;
  }
  .dish-name,.dish-price{font-family:"Tinos","Times New Roman",serif;font-weight:700;font-size:8.5px;line-height:10px;margin:0}
  .dish-desc{font-size:6.6px;line-height:8.6px;margin:6px 0 0}
  .brand-name{
    position:absolute;right:8px;bottom:10px;
    color:var(--accent);font-family:"Arimo",Arial,sans-serif;font-size:11px;line-height:12px;
  }
</style>
</head>
<body>

<section class="menu-panel panel-left">
  <h2 class="section-title" style="--x:170;--y:25">Chicken</h2>
  <div class="dish" style="--x:68;--y:50"><p class="dish-name">General Tso's Chicken</p><p class="dish-price">$ 11.75</p><p class="dish-desc">Crispy dark meat chicken with chili peppers in a spicy tangerine sauce topped with scallions.</p></div>
  <div class="dish" style="--x:267;--y:50"><p class="dish-name">Chicken Lettuce Cups</p><p class="dish-price">$ 11.75</p><p class="dish-desc">Minced white meat chicken with bell peppers, water chestnuts, black mushrooms, pine nuts, and white crunchies. Served with four lettuce cups.</p></div>
  <div class="dish" style="--x:165;--y:118"><p class="dish-name">Moo Goo Gai Pan</p><p class="dish-price">$ 00</p></div>
  <div class="dish" style="--x:71;--y:150"><p class="dish-name">Orange Chicken</p><p class="dish-price">$ 11.95</p><p class="dish-desc">Crispy chicken breast with onions and red and green bell peppers in a tangy orange Sauce.</p></div>
  <div class="dish" style="--x:261;--y:150"><p class="dish-name">Kung Pao Chicken</p><p class="dish-price">$ 11.95</p><p class="dish-desc">Dark meat chicken with red bell peppers, peanuts and water chestnuts in picy red sauce.</p></div>
  <h2 class="section-title" style="--x:170;--y:225">Beef/Pork</h2>
  <div class="dish" style="--x:70;--y:253"><p class="dish-name">Mongolian Beef</p><p class="dish-price">$ 12.25</p><p class="dish-desc">Flank steak, garlic, ginger, and green onions on a bed of white crunchies.</p></div>
  <div class="dish" style="--x:256;--y:253"><p class="dish-name">Pepper Steak</p><p class="dish-price">$ 11.95</p><p class="dish-desc">Flank steak, bell peppers onions and garlic in black pepper sauce.</p></div>
  <div class="dish" style="--x:165;--y:316"><p class="dish-name">Sweet &amp; Sour Pork</p><p class="dish-price">$ 00</p></div>
  <div class="dish" style="--x:65;--y:351"><p class="dish-name">Beef &amp; Broccoli</p><p class="dish-price">$ 11.95</p><p class="dish-desc">Flank steak, broccoli, and black mushrooms sautéed in a garlic brown sauce.</p></div>
  <div class="dish" style="--x:260;--y:351"><p class="dish-name">Sliced BBQ Pork</p><p class="dish-price">$ 8.95</p><p class="dish-desc">Tender slices of juicy pork opped with scallions in a barbeque sauce.</p></div>
  <span class="brand-name">Lo Mara</span>
</section>

<section class="menu-panel panel-middle">
  <h2 class="section-title" style="--x:165;--y:41">Seafood</h2>
  <div class="dish" style="--x:59;--y:67"><p class="dish-name">Shrimp w/ Snow Peas</p><p class="dish-price">$ 13.95</p><p class="dish-desc">Large shrimp with snow peas water chestnuts carrots and ginger in a white wine sauce.</p></div>
  <div class="dish" style="--x:257;--y:67"><p class="dish-name">Fish w/ ginger soy</p><p class="dish-price">$ 15.95</p><p class="dish-desc">Whole white fish filet steamed with ginger and topped with green onions and cilantro.</p></div>
  <div class="dish" style="--x:168;--y:120"><p class="dish-name">Scallops<br>w/ black bean sauce</p><p class="dish-price">$ 00</p></div>
  <div class="dish" style="--x:72;--y:157"><p class="dish-name">Kung Pao 3 treasures</p><p class="dish-price">$ 13.95</p><p class="dish-desc">Large shrimp, beef, and chicken breast with scallions, peanuts water chestnuts and chili peppers. Prepared mandarin-Style.</p></div>
  <div class="dish" style="--x:256;--y:157"><p class="dish-name">Honey Walnut Shrimp</p><p class="dish-price">$ 13.95</p><p class="dish-desc">Lightly crisped savory shrimp with honey-Glazed walnuts.</p></div>
  <h2 class="section-title" style="--x:168;--y:240">Vegetables</h2>
  <div class="dish" style="--x:72;--y:283"><p class="dish-name">Bak Choy w/ Mushrooms</p><p class="dish-price">$ 6.95</p><p class="dish-desc">Baby bokchoy and black mushrooms sautéed in a brown sauce.</p></div>
  <div class="dish" style="--x:269;--y:283"><p class="dish-name">Spicy Garlic Eggplant</p><p class="dish-price">$ 8.95</p><p class="dish-desc">Sautéed chinese eggplant, red onions and scallions in a spicy garlic sauce.</p></div>
  <div class="dish" style="--x:169;--y:323"><p class="dish-name">Spinach w/ garlic</p><p class="dish-price">$ 6.95</p><p class="dish-desc">Sautéed spinach with garlic.</p></div>
  <div class="dish" style="--x:66;--y:355"><p class="dish-name">Schezuan String Bean</p><p class="dish-price">$ 8.95</p><p class="dish-desc">Blue lake green beans and garlic sautéed with pickled szechwan vegetables.</p></div>
  <div class="dish" style="--x:265;--y:355"><p class="dish-name">Fragrant Vegetables</p><p class="dish-price">$ 8.95</p><p class="dish-desc">Mixed vegetables with white wine, curry, garlic, black bean kungpao, or vegetarian sauce.</p></div>
  <span class="brand-name">Lo Mara</span>
</section>

<section class="menu-panel panel-right">
  <h2 class="section-title" style="--x:165;--y:33">Noodles</h2>
  <div class="dish" style="--x:75;--y:57"><p class="dish-name">Chow Mein</p><p class="dish-price">$ 12.95</p><p class="dish-desc">Crispy egg noodles or soft lo mein noodles with large vegetables and chicken, pork or vegetables. Beef or shrimp instead add $1.00.</p></div>
  <div class="dish" style="--x:261;--y:57"><p class="dish-name">Lo Mein</p><p class="dish-price">$ 10.95</p><p class="dish-desc">Soft lo mein noodles with shredded vegetables and chicken, pork, or vegetables. Beef or shrimp instead add $1.00.</p></div>
  <div class="dish" style="--x:169;--y:135"><p class="dish-name">Seafood Noodles</p><p class="dish-price">$ 00</p></div>
  <div class="dish" style="--x:77;--y:167"><p class="dish-name">Singapore Noodles</p><p class="dish-price">$ 10.95</p><p class="dish-desc">Shrimp, barbeque pork, bean sprouts, onions, egg, and bell peppers with rice noodles in a curry sauce</p></div>
  <div class="dish" style="--x:258;--y:167"><p class="dish-name">Pad Thai</p><p class="dish-price">$ 12.95</p><p class="dish-desc">Rice noodles with chicken shrimp eggs, onions, and scallions topped with peanuts and cilantro.</p></div>
  <span class="brand-name">Lo Mara</span>
</section>

</body>
</html>
```